New Website

New website is to be the same as Amber Lantern.

Website needs to be fully functional, with only text and logo to be added by client at a later date.

Logo has been added for reference.

```html
<!DOCTYPE html>
<html lang="en">
<head>
<meta charset="utf-8">
<title>Velmora – Avenues for business growth</title>
<link href="https://fonts.googleapis.com/css2?family=Roboto:wght@300;400;500;700&family=Open+Sans:wght@400;600&display=swap" rel="stylesheet">
<style>
:root{
  --blue:#1a5fc1;
  --blue-dark:#134a99;
  --ink:#222629;
  --text:#555;
  --muted:#777;
  --black:#151617;
  --topbar:#1c1d1f;
  --grey-bg:#f6f6f6;
  --gold:#d9ab22;
  --white:#fff;
  --line:#e1e1e1;
}
*{margin:0;padding:0;box-sizing:border-box}
html,body{width:1200px;height:2830px;overflow:hidden;background:var(--white)}
body{font-family:"Open Sans",Arial,sans-serif;color:var(--text);position:relative}
.heading{font-family:"Roboto",Arial,sans-serif}

/* top bar */
.topbar{height:68px;background:var(--topbar);position:relative}
.login{position:absolute;left:674px;top:17px;width:153px;height:34px;background:var(--gold);border-radius:3px;color:#fff;font:400 15px "Roboto",sans-serif;display:flex;align-items:center;justify-content:center;gap:8px}
.social{position:absolute;left:883px;top:18px;display:flex;gap:10px}
.social span{width:28px;height:28px;border:2px solid #fff;border-radius:50%}

/* header */
.header{height:106px;position:relative;border-bottom:1px solid var(--line)}
.brand{position:absolute;left:180px;top:22px;display:flex;align-items:center;gap:14px}
.brand-mark{width:56px;height:56px;border-radius:50%;background:var(--blue)}
.brand-name{font:400 30px "Roboto",sans-serif;color:var(--blue-dark);letter-spacing:1px}
.nav{position:absolute;right:156px;top:46px;display:flex;font:500 13px "Roboto",sans-serif;color:#333}
.nav a{color:inherit;text-decoration:none;padding:0 12px;border-right:1px solid #333;line-height:12px}
.nav a:last-child{border:0;padding-right:0}

/* hero */
.hero{height:607px;position:relative;background:linear-gradient(100deg,#4a4548 0%,#6f6a70 35%,#b7b2b4 60%,#8d8588 80%,#3e3a3c 100%)}
.hero-text{position:absolute;left:184px;top:180px;color:#fff}
.hero-title{font:400 40px "Roboto",sans-serif}
.hero-sub{font:400 25px "Roboto",sans-serif;margin-top:2px}
.hero-body{font:500 20px/30px "Roboto",sans-serif;margin-top:26px;width:560px}
.btn-read{display:inline-block;margin-top:40px;background:#fff;color:#222;font:500 20px "Roboto",sans-serif;padding:16px 30px;border-radius:3px}
.hero-arrows{position:absolute;left:188px;top:488px;display:flex;gap:14px}
.hero-arrows span{width:34px;height:34px;border-radius:50%;background:rgba(0,0,0,.45);display:flex;align-items:center;justify-content:center}

/* intro */
.intro{height:359px;position:relative}
.intro-photo{position:absolute;left:172px;top:68px;width:383px;height:219px;background:linear-gradient(120deg,#c8d3de,#8b98a6 55%,#e6e0da);border:4px solid #fff;box-shadow:0 2px 6px rgba(0,0,0,.35)}
.intro-text{position:absolute;left:587px;top:62px;width:430px}
.intro-title{font:400 27px/36px "Roboto",sans-serif;color:var(--ink)}
.intro-title strong{display:block;font-weight:400;font-size:31px;color:var(--blue)}
.intro-text p{font-size:12px;line-height:22px;color:var(--muted);margin-top:14px}

/* services */
.services{height:426px;background:var(--grey-bg);border-top:1px solid var(--line);border-bottom:1px solid var(--line);text-align:center;position:relative}
.section-title{font:700 32px "Roboto",sans-serif;color:var(--blue)}
.services .section-title{padding-top:22px}
.services-sub{font-size:17px;color:#444;margin-top:6px}
.pager{display:flex;justify-content:center;gap:8px;margin-top:18px}
.pager span{width:20px;height:20px;border:1px solid #ccc;background:#fff}
.service-list{position:absolute;top:120px;left:160px;display:flex}
.service{width:220px;text-align:center;margin-right:5px}
.service-icon{width:146px;height:146px;margin:0 auto;border-radius:50%;background:var(--blue);border:6px solid #e9e9e9;display:flex;align-items:center;justify-content:center}
.service-icon.dark{background:var(--black)}
.service h3{font:400 15px "Roboto",sans-serif;color:#222;margin-top:32px}
.service p{font-size:10.5px;line-height:19px;color:var(--muted);margin-top:12px;padding:0 20px}

/* divider */
.divider{width:360px;height:12px;margin:12px auto 0;position:relative}
.divider::before{content:"";position:absolute;left:0;right:0;top:6px;height:1px;background:linear-gradient(90deg,transparent,#999,transparent)}
.divider::after{content:"";position:absolute;left:50%;top:2px;width:9px;height:9px;background:var(--blue);transform:translateX(-50%) rotate(45deg)}

/* team */
.team{height:576px;text-align:center;position:relative}
.team .section-title{padding-top:34px;font-size:30px}
.team-grid{position:absolute;left:174px;top:125px;width:856px;display:grid;grid-template-columns:repeat(4,214px);grid-auto-rows:214px}
.photo{background:linear-gradient(135deg,#d9d4cf,#9aa3ad)}
.photo.b{background:linear-gradient(135deg,#e7eef5,#7d93b0)}
.photo.c{background:linear-gradient(135deg,#8c8c8c,#d2d2d2)}
.photo.d{background:linear-gradient(135deg,#37414d,#8e9aa6)}
.member{color:#fff;display:flex;flex-direction:column;align-items:center;justify-content:center}
.member.blue{background:var(--blue)}
.member.black{background:var(--black)}
.member-icons{display:flex;gap:12px;margin-bottom:20px}
.member-icons span{width:30px;height:30px;border:2px solid #fff;border-radius:50%;display:flex;align-items:center;justify-content:center}
.member h3{font:700 20px "Roboto",sans-serif}
.member p{font-size:12px;margin-top:10px}

/* blogs */
.blogs{height:421px;background:var(--grey-bg);position:relative;text-align:center}
.blogs .section-title{padding-top:22px;font-size:30px}
.blog-list{position:absolute;left:174px;top:115px;display:flex;gap:28px}
.blog{width:266px;text-align:left;position:relative}
.blog-photo{height:145px;border:2px solid #fff;box-shadow:0 0 0 1px #ddd;background:linear-gradient(135deg,#c7d6e6,#6f87a4)}
.blog-photo.b{background:linear-gradient(135deg,#e4eef8,#5d7a9c)}
.blog-photo.c{background:linear-gradient(135deg,#f0f0f0,#9fb7c6)}
.date{position:absolute;left:0;top:157px;width:46px;height:52px;background:var(--blue);color:#fff;text-align:center;font:400 22px/28px "Roboto",sans-serif}
.date small{display:block;font-size:12px;line-height:16px}
.date-tag{position:absolute;left:0;top:209px;width:46px;height:30px;background:#555;display:flex;align-items:center;justify-content:center}
.blog-body{margin-left:70px;padding-top:14px}
.blog h3{font:400 16px "Roboto",sans-serif;color:#333}
.blog p{font-size:10.5px;line-height:19px;color:#666;margin-top:12px;text-align:justify}

/* footer */
.footer{height:198px;background:var(--black);position:relative;color:#aaa}
.footer h4{font:400 16px "Roboto",sans-serif;color:#ddd;letter-spacing:.5px}
.f-services{position:absolute;left:172px;top:22px}
.f-cols{display:flex;gap:40px;margin-top:18px}
.f-cols ul{list-style:none;font-size:10px;line-height:21px;color:#999}
.f-cols li::before{content:"›";margin-right:8px;color:#ccc}
.f-contact{position:absolute;left:569px;top:28px}
.contact-row{display:flex;align-items:center;gap:16px;margin-top:10px;font-size:11px;line-height:16px}
.contact-row:first-of-type{margin-top:16px}
.contact-icon{width:30px;height:30px;background:#2a2b2d;display:flex;align-items:center;justify-content:center;flex:none}
.contact-row.phone{color:var(--blue);font-size:13px}
.f-news{position:absolute;left:835px;top:28px;width:196px}
.f-news p{font-size:10px;line-height:18px;color:#888;margin-top:14px}
.news-form{display:flex;margin-top:12px}
.news-input{flex:1;height:30px;background:#202124;font-size:9px;color:#777;padding:9px 12px}
.news-btn{width:38px;height:30px;background:var(--blue);display:flex;align-items:center;justify-content:center}
.bottombar{height:69px;background:#0d0d0e;position:relative;font-size:10px;color:#777}
.copy{position:absolute;left:174px;top:30px}
.foot-social{position:absolute;left:886px;top:22px;display:flex;gap:6px}
.foot-social span{width:22px;height:22px;border:1px solid #666;border-radius:50%}
.page-tag{position:absolute;left:1128px;top:30px;color:#999}
</style>
</head>
<body>

<div class="topbar">
  <div class="login">
    <svg width="14" height="15" viewBox="0 0 14 15"><circle cx="7" cy="4" r="3.5" fill="#fff"/><path d="M0 15c0-4 3-6 7-6s7 2 7 6z" fill="#fff"/></svg>
    Client Login
  </div>
  <div class="social" aria-label="Social links"><span></span><span></span><span></span><span></span></div>
</div>

<header class="header">
  <div class="brand"><span class="brand-mark"></span><span class="brand-name">Velmora</span></div>
  <nav class="nav"><a>Home</a><a>About Us</a><a>Client Services</a><a>Testimonials</a><a>Services</a><a>Blog</a><a>Contact Us</a></nav>
</header>

<section class="hero" role="img" aria-label="Businesswoman on the phone in an office">
  <div class="hero-text">
    <h1 class="hero-title">Avenues for business growth</h1>
    <p class="hero-sub">Lorem Ipsum is simply dummy</p>
    <p class="hero-body">Sed purus purus, tincidunt eget malesuada et, molestie ut eros. Fusce blandit, sapien eu sollicitudin consectetur,</p>
    <span class="btn-read">READ MORE</span>
  </div>
  <div class="hero-arrows">
    <span><svg width="10" height="12"><path d="M8 1L2 6l6 5" stroke="#fff" stroke-width="2" fill="none"/></svg></span>
    <span><svg width="10" height="12"><path d="M2 1l6 5-6 5" stroke="#fff" stroke-width="2" fill="none"/></svg></span>
  </div>
</section>

<section class="intro">
  <div class="intro-photo" role="img" aria-label="Business team meeting around a table"></div>
  <div class="intro-text">
    <h2 class="intro-title">INTRODUCING YOUR BUSINESS <strong>EXPERT NETWORK</strong></h2>
    <p>Brisk Studio est une agence web de Lacroix spécialisée dans la conception de site Web au design responsive. Fondée en 2012 par deux frères, l'entreprise a comme objectif principal de créer des sites web dynamiques, modernes et accessibles sur tous les appareils électroniques.</p>
    <p>Brisk Studio c'est l'assurance de jouir de précieux conseils! C'est la certitude d'avoir un site web à votre image et à la hauteur de vos attentes. Finalement, c'est une solution clés en main qui saura vous apporter satisfaction!</p>
  </div>
</section>

<section class="services">
  <h2 class="section-title">SERVICES</h2>
  <p class="services-sub">Résumez votre produit Quelle est All About</p>
  <div class="pager"><span></span><span></span></div>
  <div class="service-list">
    <div class="service">
      <div class="service-icon"><svg width="64" height="50" viewBox="0 0 64 50" fill="none" stroke="#fff" stroke-width="6" stroke-linecap="round"><path d="M4 18a40 40 0 0 1 56 0"/><path d="M14 28a26 26 0 0 1 36 0"/><path d="M24 38a12 12 0 0 1 16 0"/></svg></div>
      <h3>PRE-SESSION DISCOVERY</h3>
      <p>Qu'est-ce que SitePress? SitePress se classe numéro 1 comme solution de gestion de contenu (CMS)</p>
    </div>
    <div class="service">
      <div class="service-icon dark"><svg width="60" height="54" viewBox="0 0 60 54" fill="none" stroke="#fff" stroke-width="3"><rect x="3" y="3" width="48" height="34" rx="2"/><path d="M20 46h14M27 37v9"/><circle cx="27" cy="20" r="7"/><rect x="46" y="34" width="11" height="17" rx="5" fill="#fff"/></svg></div>
      <h3>ONE+-ON-ONE SESSION</h3>
      <p>Qu'est-ce que SitePress? SitePress se classe numéro 1 comme solution de gestion de contenu (CMS)</p>
    </div>
    <div class="service">
      <div class="service-icon"><svg width="66" height="60" viewBox="0 0 66 60"><circle cx="38" cy="24" r="17" fill="none" stroke="#fff" stroke-width="8" stroke-dasharray="6 4.7"/><circle cx="38" cy="24" r="7" fill="#fff"/><circle cx="16" cy="44" r="10" fill="none" stroke="#fff" stroke-width="6" stroke-dasharray="4 3.9"/></svg></div>
      <h3>SESSION SUMMARY REPORT</h3>
      <p>Qu'est-ce que SitePress? SitePress se classe numéro 1 comme solution de gestion de contenu (CMS)</p>
    </div>
    <div class="service">
      <div class="service-icon"><svg width="70" height="50" viewBox="0 0 70 50" fill="#fff" stroke="#1a5fc1" stroke-width="2"><path d="M12 8l12-6 12 6-12 6z"/><path d="M12 8v12l12 6V14z"/><path d="M36 8v12l-12 6V14z"/><path d="M34 22l12-6 12 6-12 6z"/><path d="M34 22v12l12 6V28z"/><path d="M58 22v12l-12 6V28z"/></svg></div>
      <h3>POST-SESSION OPTIONS</h3>
      <p>Qu'est-ce que SitePress? SitePress se classe numéro 1 comme solution de gestion de contenu (CMS)</p>
    </div>
  </div>
</section>

<section class="team">
  <h2 class="section-title">Our Team</h2>
  <div class="divider"></div>
  <div class="team-grid">
    <div class="photo" role="img" aria-label="Team member portrait at a desk"></div>
    <div class="member black">
      <div class="member-icons"><span><svg width="12" height="12"><circle cx="5" cy="5" r="3.5" stroke="#fff" stroke-width="1.5" fill="none"/><path d="M8 8l3 3" stroke="#fff" stroke-width="1.5"/></svg></span><span><svg width="12" height="12"><path d="M4 8l4-4M2 6l2-2 2 2M6 10l2-2" stroke="#fff" stroke-width="1.5" fill="none"/></svg></span></div>
      <h3>Adrien Voss</h3><p>Maecenas tristique sem</p>
    </div>
    <div class="photo b" role="img" aria-label="Team member portrait with a laptop"></div>
    <div class="member blue">
      <div class="member-icons"><span><svg width="12" height="12"><circle cx="5" cy="5" r="3.5" stroke="#fff" stroke-width="1.5" fill="none"/><path d="M8 8l3 3" stroke="#fff" stroke-width="1.5"/></svg></span><span><svg width="12" height="12"><path d="M4 8l4-4M2 6l2-2 2 2M6 10l2-2" stroke="#fff" stroke-width="1.5" fill="none"/></svg></span></div>
      <h3>Lena Marsh</h3><p>Maecenas tristique sem</p>
    </div>
    <div class="member blue">
      <div class="member-icons"><span><svg width="12" height="12"><circle cx="5" cy="5" r="3.5" stroke="#fff" stroke-width="1.5" fill="none"/><path d="M8 8l3 3" stroke="#fff" stroke-width="1.5"/></svg></span><span><svg width="12" height="12"><path d="M4 8l4-4M2 6l2-2 2 2M6 10l2-2" stroke="#fff" stroke-width="1.5" fill="none"/></svg></span></div>
      <h3>Tobin Hale</h3><p>Maecenas tristique sem</p>
    </div>
    <div class="photo c" role="img" aria-label="Team member portrait in a suit"></div>
    <div class="member blue">
      <div class="member-icons"><span><svg width="12" height="12"><circle cx="5" cy="5" r="3.5" stroke="#fff" stroke-width="1.5" fill="none"/><path d="M8 8l3 3" stroke="#fff" stroke-width="1.5"/></svg></span><span><svg width="12" height="12"><path d="M4 8l4-4M2 6l2-2 2 2M6 10l2-2" stroke="#fff" stroke-width="1.5" fill="none"/></svg></span></div>
      <h3>Rowan Pike</h3><p>Maecenas tristique sem</p>
    </div>
    <div class="photo d" role="img" aria-label="Team member portrait in the city"></div>
  </div>
</section>

<section class="blogs">
  <h2 class="section-title">Latest Blogs</h2>
  <div class="divider"></div>
  <div class="blog-list">
    <article class="blog">
      <div class="blog-photo" role="img" aria-label="Colleagues reviewing work on a laptop"></div>
      <div class="date">15<small>Jan</small></div>
      <div class="date-tag"><svg width="14" height="12"><path d="M1 1h12v7H6l-3 3V8H1z" fill="#fff"/></svg></div>
      <div class="blog-body"><h3>Morbi tempor quam</h3><p>Lorem ipsum dolor sit amet, consectetur adipiscing elit, sed do eiusmod tempor incididunt ut labore et dolore magna aliqua. Ut enim ad minim</p></div>
    </article>
    <article class="blog">
      <div class="blog-photo b" role="img" aria-label="Business team in a meeting"></div>
      <div class="date">15<small>Jan</small></div>
      <div class="date-tag"><svg width="14" height="12"><path d="M1 1h12v7H6l-3 3V8H1z" fill="#fff"/></svg></div>
      <div class="blog-body"><h3>Morbi tempor quam</h3><p>Lorem ipsum dolor sit amet, consectetur adipiscing elit, sed do eiusmod tempor incididunt ut labore et dolore magna aliqua. Ut enim ad minim</p></div>
    </article>
    <article class="blog">
      <div class="blog-photo c" role="img" aria-label="Woman reading on a tablet"></div>
      <div class="date">15<small>Jan</small></div>
      <div class="date-tag"><svg width="14" height="12"><path d="M1 1h12v7H6l-3 3V8H1z" fill="#fff"/></svg></div>
      <div class="blog-body"><h3>Morbi tempor quam</h3><p>Lorem ipsum dolor sit amet, consectetur adipiscing elit, sed do eiusmod tempor incididunt ut labore et dolore magna aliqua. Ut enim ad minim</p></div>
    </article>
  </div>
</section>

<footer class="footer">
  <div class="f-services">
    <h4>SERVICES</h4>
    <div class="f-cols">
      <ul><li>Sites SitePress</li><li>Sites adaptatifs</li><li>Image de marque</li><li>Hébergement</li><li>Campagne publicitaire</li><li>Rédaction et traduction</li></ul>
      <ul><li>Commerce en ligne</li><li>Infolettre</li><li>Statistiques sur les visiteurs</li><li>Réseaux sociaux</li><li>Référencement et positionnement</li></ul>
    </div>
  </div>
  <div class="f-contact">
    <h4>GET IN TOUCH</h4>
    <div class="contact-row"><span class="contact-icon"><svg width="12" height="16"><path d="M6 15s5-6 5-9.5A5 5 0 0 0 1 5.5C1 9 6 15 6 15z" fill="#999"/><circle cx="6" cy="5.5" r="2" fill="#2a2b2d"/></svg></span><span>22 Rue des Pins, Lacroix,<br>Québec (QC) A1B 2C3</span></div>
    <div class="contact-row phone"><span class="contact-icon"><svg width="14" height="14"><path d="M3 1l3 3-2 2a8 8 0 0 0 4 4l2-2 3 3-2 2C6 13 1 8 1 3z" fill="#999"/></svg></span><span>555-014-2277</span></div>
    <div class="contact-row"><span class="contact-icon"><svg width="14" height="10"><rect x=".5" y=".5" width="13" height="9" fill="none" stroke="#999"/><path d="M1 1l6 5 6-5" stroke="#999" fill="none"/></svg></span><span>info@velmora.com</span></div>
  </div>
  <div class="f-news">
    <h4>NEWSLETTER</h4>
    <p>Neque porro quisquam est, qui dolorem ipsum quia dolor sit amet, consectetur adipisci velit.</p>
    <div class="news-form"><span class="news-input">Email address</span><span class="news-btn"><svg width="14" height="10"><path d="M0 5h10M7 1l4 4-4 4" stroke="#fff" stroke-width="2" fill="none"/></svg></span></div>
  </div>
</footer>

<div class="bottombar">
  <p class="copy">Copy rights 2015 Velmora. All Rights Reserved.</p>
  <div class="foot-social" aria-label="Social links"><span></span><span></span><span></span><span></span><span></span></div>
  <span class="page-tag">D2</span>
</div>

</body>
</html>
```